Statement of Capabilities

We are looking for a fresh new stationary (Word Template) and a new look for our statement of capabilities....logo must be the same.

We are an electrical / lighting contractor-

www.BrightfoldServices.com

Target Market(s)

B2B and government agencies

Industry/Entity Type

Electrical

Colors
eb1f27
0655a3

Requirements
Must have
• LOGO

```html
<!DOCTYPE html>
<html lang="en">
<head>
<meta charset="utf-8">
<title>Brightfold Services Stationery</title>
<link rel="stylesheet" href="https://fonts.googleapis.com/css2?family=Montserrat:wght@500;700;800&family=Questrial&display=swap">
<style>
:root{
  --brand-red:#eb1f27;
  --brand-blue:#23439e;
  --paper:#f7f7f7;
  --ink:#555a60;
  --backdrop:#e6e6e6;
  --rule:#c9ccd3;
}
*{box-sizing:border-box;margin:0;padding:0}
html,body{width:1200px;height:800px;overflow:hidden}
body{background:var(--backdrop);font-family:"Questrial",sans-serif;color:var(--ink);position:relative}
.piece{position:absolute;background:var(--paper);overflow:hidden}
.wordmark{font-family:"Montserrat",sans-serif;font-weight:800;color:var(--brand-red);line-height:1.05;text-transform:uppercase;letter-spacing:.5px}
.wordmark small{display:block;font-size:.62em}
.address{font-size:6px;line-height:1.55}
.footer-band{position:absolute;left:0;right:0;bottom:0;height:5px;background:var(--brand-red)}
.url-tab{position:absolute;bottom:5px;background:var(--brand-blue);color:#fff;font-size:6.5px;padding:2px 10px 2px;border-radius:6px 6px 0 0;white-space:nowrap}
.services{font-family:"Montserrat",sans-serif;font-weight:700;text-transform:uppercase;color:var(--brand-blue);font-size:5.2px;letter-spacing:.2px;white-space:nowrap}
.contact-line{display:flex;align-items:center;gap:4px;font-size:5.5px}
.icon{width:6px;height:6px;flex:none}

/* envelope back */
.envelope-back{left:120px;top:96px;width:410px;height:210px}
.envelope-back .flap{position:absolute;left:0;top:0;width:100%;height:68px;background:var(--brand-blue);border-radius:0 0 14px 14px;color:#fff;font-size:6px;text-align:center;padding-top:22px}

/* envelope front */
.envelope-front{left:80px;top:290px;width:455px;height:228px;box-shadow:0 0 0 1px #ddd}
.envelope-front .wordmark{position:absolute;left:26px;top:26px;font-size:15px}
.envelope-front .address{position:absolute;left:50px;top:76px}
.envelope-front .url-tab{left:32px}

/* business cards */
.card{top:595px;width:190px;height:106px}
.card-front{left:100px}
.card-front .wordmark{position:absolute;left:14px;top:34px;font-size:10px}
.card-front .person{position:absolute;left:116px;top:20px}
.person-name{font-family:"Montserrat",sans-serif;font-weight:700;color:var(--brand-blue);font-size:6.5px;letter-spacing:.4px}
.person-title{font-size:4.8px;margin-bottom:6px}
.card-front .contact-line{margin-bottom:2px;font-size:4.6px}
.card-front .icon{width:5px;height:5px}
.card-front .address{font-size:4.6px;margin-top:4px}
.card-front .footer-band{height:3px}
.card-front .url-tab{left:16px;bottom:3px;font-size:4.8px;padding:1px 8px}
.card-back{left:314px;background:var(--brand-blue)}
.card-back .wordmark{position:absolute;left:0;right:0;top:20px;text-align:center;font-size:12px}
.card-back .services{position:absolute;left:8px;right:8px;top:80px;color:#fff;font-size:4.2px;text-align:center;line-height:1.9}
.card-back .services hr{border:0;border-top:.5px solid rgba(255,255,255,.5)}

/* letterhead */
.letterhead{left:628px;top:76px;width:488px;height:640px;box-shadow:0 0 0 1px #ddd}
.letterhead .wordmark{position:absolute;left:30px;top:38px;font-size:16px}
.letterhead .services{position:absolute;left:232px;right:30px;top:48px;line-height:2}
.letterhead .services hr{border:0;border-top:.6px solid var(--rule)}
.letterhead .contact-row{position:absolute;left:32px;bottom:24px;display:flex;gap:22px;align-items:center}
.letterhead .url-tab{right:40px;font-size:6.8px;padding:2px 14px}
</style>
</head>
<body>

<section class="piece envelope-back" aria-label="Envelope back">
  <div class="flap">www.BrightfoldServices.com</div>
</section>

<section class="piece envelope-front" aria-label="Envelope front">
  <div class="wordmark">Brightfold<small>Services</small></div>
  <p class="address">415 Harbor Lane Suite B<br>Fairmont Valley 20190</p>
  <div class="url-tab">www.BrightfoldServices.com</div>
  <div class="footer-band"></div>
</section>

<section class="piece card card-front" aria-label="Business card front">
  <div class="wordmark">Brightfold<small>Services</small></div>
  <div class="person">
    <p class="person-name">DANA MARLOWE</p>
    <p class="person-title">Managing Director</p>
    <p class="contact-line"><svg class="icon" viewBox="0 0 10 10"><rect width="10" height="10" rx="1.5" fill="#eb1f27"/><path d="M3 2.2l1.2 1.6-.7.8c.4.9 1 1.5 1.9 1.9l.8-.7 1.6 1.2-.7 1.1C4.6 8 2 5.4 2 2.9z" fill="#fff"/></svg>800-555-0142</p>
    <p class="contact-line"><svg class="icon" viewBox="0 0 10 10"><rect width="10" height="10" rx="1.5" fill="#eb1f27"/><rect x="2.2" y="4" width="5.6" height="3.6" fill="#fff"/><rect x="3.2" y="2.2" width="3.6" height="1.5" fill="#fff"/></svg>800-555-0143</p>
    <p class="address">415 Harbor Lane Suite B<br>Fairmont Valley 20190</p>
  </div>
  <div class="url-tab">www.BrightfoldServices.com</div>
  <div class="footer-band"></div>
</section>

<section class="piece card card-back" aria-label="Business card back">
  <div class="wordmark">Brightfold<small>Services</small></div>
  <div class="services">
    <p>Street · Site Safety · Retail · Field Lighting · Wiring</p>
    <hr>
    <p>Cedar Point · Oakhaven · Ridgeview · Fairmont Valley</p>
  </div>
</section>

<section class="piece letterhead" aria-label="Letterhead">
  <div class="wordmark">Brightfold<small>Services</small></div>
  <div class="services">
    <p>Street · Site Safety · Retail · Field Lighting · Wiring · Capital Region</p>
    <hr>
    <p>Cedar Point · Oakhaven · Ridgeview · Fairmont Valley</p>
  </div>
  <div class="contact-row">
    <span class="address">415 Harbor Lane Suite B, Fairmont Valley 20190</span>
    <span class="contact-line"><svg class="icon" viewBox="0 0 10 10"><rect width="10" height="10" rx="1.5" fill="#eb1f27"/><path d="M3 2.2l1.2 1.6-.7.8c.4.9 1 1.5 1.9 1.9l.8-.7 1.6 1.2-.7 1.1C4.6 8 2 5.4 2 2.9z" fill="#fff"/></svg>800-555-0142</span>
    <span class="contact-line"><svg class="icon" viewBox="0 0 10 10"><rect width="10" height="10" rx="1.5" fill="#eb1f27"/><rect x="2.2" y="4" width="5.6" height="3.6" fill="#fff"/><rect x="3.2" y="2.2" width="3.6" height="1.5" fill="#fff"/></svg>800-555-0143</span>
  </div>
  <div class="url-tab">www.BrightfoldServices.com</div>
  <div class="footer-band"></div>
</section>

</body>
</html>
```